Machining Business Order Thank You Insert

I am looking for a business style card to include with orders that I ship. The card needs to thank the recipient for their order, and encourage them to leave a review. The card should include my business name and contact information and have an area to hand write a message.

I mainly sale on Craftlane and my own website. We are a machining an manufacturing business that are in the sale of mostly metal machined and 3d printed plastic products.

The front of the card should include the following:
Logo: (attached)
Snapgram: https://www.snapgram.example/kelvomill/
Friendsbook: https://www.friendsbook.example/KelvoMill
Website: https://www.kelvomill.example/

The back of the card needs an area to write a message

Industry/Entity Type

3D Printing, Machining, Craftlane

Contact Information for Business Card

Black or white front, white back to write a personal message

Font styles to use
Sans Serif

Colors

Designer to choose colors to be used in the design.

Requirements
Must have
• Encourage a review, social media info

```html
<!DOCTYPE html>
<html lang="en">
<head>
<meta charset="utf-8">
<title>KelvoMill Thank You Insert</title>
<link rel="stylesheet" href="https://fonts.googleapis.com/css2?family=Montserrat:wght@700&family=Questrial&family=Patrick+Hand&display=swap">
<style>
  :root {
    --page: #ffffff;
    --card-dark: #000000;
    --card-light: #ffffff;
    --accent: #ef5a2a;
    --ink-light: #ffffff;
    --ink-dark: #111111;
    --hairline: #e4e4e4;
  }
  * { margin: 0; padding: 0; box-sizing: border-box; }
  html, body {
    width: 1200px;
    height: 957px;
    overflow: hidden;
    background: var(--page);
  }
  .canvas {
    position: relative;
    width: 1200px;
    height: 957px;
  }
  .card {
    position: absolute;
    left: 325px;
    width: 485px;
    height: 277px;
    border-radius: 30px;
    overflow: hidden;
  }
  .card--front {
    top: 131px;
    background: var(--card-dark);
    color: var(--ink-light);
  }
  .card--back {
    top: 462px;
    background: var(--card-light);
    color: var(--ink-dark);
    border: 1px solid var(--hairline);
  }
  .thanks-title {
    position: absolute;
    top: 30px;
    left: 0;
    width: 100%;
    text-align: center;
    font-family: "Montserrat", sans-serif;
    font-weight: 700;
    font-size: 50px;
    letter-spacing: 4px;
    color: var(--accent);
    line-height: 1;
  }
  .thanks-subtitle {
    position: absolute;
    top: 92px;
    left: 0;
    width: 100%;
    text-align: center;
    font-family: "Questrial", sans-serif;
    font-size: 11px;
    letter-spacing: 15.5px;
    padding-left: 15px;
    line-height: 1;
  }
  .review-prompt {
    position: absolute;
    top: 152px;
    left: 0;
    width: 100%;
    text-align: center;
    font-family: "Patrick Hand", cursive;
    font-size: 27px;
    letter-spacing: 1px;
    line-height: 1;
  }
  .brand {
    position: absolute;
    left: 36px;
    top: 80px;
    width: 140px;
    display: flex;
    flex-direction: column;
    align-items: center;
    gap: 22px;
  }
  .brand__mark {
    width: 52px;
    height: 52px;
    background: var(--accent);
  }
  .brand__name {
    font-family: "Questrial", sans-serif;
    font-size: 16px;
    letter-spacing: 4px;
    color: var(--accent);
  }
  .contact-list {
    position: absolute;
    left: 237px;
    top: 108px;
    list-style: none;
    font-family: "Questrial", sans-serif;
    font-size: 12px;
  }
  .contact-list__item {
    display: flex;
    align-items: center;
    gap: 9px;
    height: 14px;
    margin-bottom: 12px;
  }
  .contact-list__icon {
    width: 14px;
    height: 14px;
    flex: none;
  }
</style>
</head>
<body>
<main class="canvas">
  <section class="card card--front">
    <h1 class="thanks-title">THANK YOU !</h1>
    <p class="thanks-subtitle">FOR SUPPORTING US</p>
    <p class="review-prompt">leave a review</p>
  </section>

  <section class="card card--back">
    <div class="brand">
      <span class="brand__mark"></span>
      <span class="brand__name">KELVOMILL</span>
    </div>
    <ul class="contact-list">
      <li class="contact-list__item">
        <svg class="contact-list__icon" viewBox="0 0 14 14" aria-hidden="true"><circle cx="7" cy="7" r="6" fill="var(--ink-dark)"/></svg>
        <span>www.friendsbook.example/KelvoMill</span>
      </li>
      <li class="contact-list__item">
        <svg class="contact-list__icon" viewBox="0 0 14 14" aria-hidden="true"><rect x="1" y="1" width="12" height="12" rx="3" fill="none" stroke="var(--ink-dark)" stroke-width="1.6"/></svg>
        <span>www.snapgram.example/kelvomill/</span>
      </li>
      <li class="contact-list__item">
        <svg class="contact-list__icon" viewBox="0 0 14 14" aria-hidden="true" fill="none" stroke="var(--ink-dark)" stroke-width="1">
          <circle cx="7" cy="7" r="6"/>
          <ellipse cx="7" cy="7" rx="2.6" ry="6"/>
          <line x1="1" y1="7" x2="13" y2="7"/>
          <line x1="2" y1="4" x2="12" y2="4"/>
          <line x1="2" y1="10" x2="12" y2="10"/>
        </svg>
        <span>www.kelvomill.example/</span>
      </li>
    </ul>
  </section>
</main>
</body>
</html>
```